Revamp Marketing Website For Video Production Website

need to revamp current website www.kestrelfilmstudio.net
reference sites www.vantora.net & http://layoutcrate.net/kestrel/
Use all current content on current kestrel website. I want a revamped modenr look. Sometbing that wows customers.
reference site www.vantora.net
Target Market(s)
business owners
Industry/Entity Type
Video Production
Number of Pages Required
5+ page
Colors
Designer to choose colors to be used in the design.
Requirements
Must have
- need to revamp current website www.kestrelfilmstudio.net
- reference sites www.vantora.net & http://layoutcrate.net/kestrel/
- Use all current content on current kestrel website. I want a revamped modenr look. Sometbing that wows customers.
- reference site www.vantora.net
Nice to have
Should not have

```html
<!DOCTYPE html>
<html lang="en">
<head>
<meta charset="utf-8">
<title>Kestrel Film Studio – Homepage Concepts</title>
<link href="https://fonts.googleapis.com/css2?family=Lato:wght@400;700;900&display=swap" rel="stylesheet">
<style>
:root{
  --board:#e4e4e4;
  --blue:#1e88e5;
  --blue-dark:#0d5fc2;
  --navy:#081426;
  --ink:#1d1d1f;
  --muted:#7a7f87;
  --light:#f3f5f8;
  --white:#ffffff;
  --faint:#e6e9ee;
  --ill-navy:#2b3148;
  --ill-grey:#d5dae2;
}
*{box-sizing:border-box;margin:0;padding:0}
html,body{width:1200px;height:2862px;overflow:hidden;background:var(--board);font-family:'Lato',sans-serif;color:var(--ink)}
.page{position:absolute;top:63px;width:488px;height:2734px;background:var(--white);overflow:hidden;box-shadow:0 0 6px rgba(0,0,0,.12)}
.page--a{left:88px}
.page--b{left:624px}
.abs{position:absolute;z-index:2}
.center{left:0;right:0;text-align:center}

/* hero */
.hero{position:absolute;left:0;top:0;width:488px;height:280px;clip-path:polygon(0 0,100% 0,100% 88%,0 100%)}
.page--a .hero{background:radial-gradient(ellipse at 50% 70%,#1b4f8f 0%,#0b2546 40%,#050c18 80%)}
.page--b .hero{background:radial-gradient(ellipse at 50% 40%,#6d7e94 0%,#2a3444 45%,#0b0f17 85%)}
.hero-accent{position:absolute;left:0;top:230px;width:488px;height:60px;background:var(--blue);clip-path:polygon(0 40%,40% 75%,0 100%)}
.nav{position:absolute;top:20px;left:28px;right:28px;height:14px;display:flex;align-items:center;z-index:2}
.logo{display:flex;align-items:center;gap:4px;color:var(--white);font-weight:900;font-size:12px;letter-spacing:1px}
.logo-mark{width:8px;height:8px;background:var(--blue)}
.logo small{display:block;font-size:3.5px;font-weight:400;letter-spacing:.4px}
.nav-links{margin-left:auto;display:flex;gap:7px;align-items:center;font-size:4.5px;color:var(--white);font-weight:700}
.nav-btn{border:1px solid var(--white);padding:2px 5px;border-radius:2px}
.nav-btn--fill{background:var(--blue);border-color:var(--blue)}
.hero-title{top:98px;color:var(--white);font-weight:900;font-size:23px;line-height:27px}
.hero-title em{font-style:normal;color:var(--blue)}
.hero-sub{top:155px;color:var(--white);font-size:6px;font-weight:700;letter-spacing:.3px}
.hero-btn{top:181px;left:194px;width:100px;height:9px;background:var(--blue);color:var(--white);font-size:4px;font-weight:700;text-align:center;line-height:9px;border-radius:1px}
.hero-note{top:203px;color:var(--white);font-size:4.5px;font-weight:700}

/* promote */
.h2{font-weight:900;font-size:14px;color:var(--ink);letter-spacing:.2px}
.kicker{color:var(--blue);font-size:5px;font-weight:700;letter-spacing:.3px}
.body{color:var(--muted);font-size:4.6px;line-height:7px}
.ghost-v{position:absolute;left:446px;top:330px;writing-mode:vertical-rl;font-weight:900;font-size:40px;color:var(--faint);letter-spacing:2px}
.create-1{left:32px;top:398px;font-weight:900;font-size:16px}
.create-2{left:32px;top:430px;color:var(--blue);font-size:8px;font-weight:700}
.create-3{left:32px;top:446px;font-weight:900;font-size:19px}
.create-4{left:32px;top:476px;color:var(--blue);font-size:8px;font-weight:700}

/* features */
.features{position:absolute;left:0;top:577px;width:488px;height:1240px;background:var(--light);clip-path:polygon(0 30px,100% 0,100% 100%,0 100%)}
.ghost{font-weight:900;font-size:38px;color:var(--faint);z-index:1}
.illus{position:absolute;z-index:1}
.illus--round{border-radius:50%;background:radial-gradient(ellipse at 50% 45%,#9aa6bb 0%,#b9c2d1 35%,var(--ill-grey) 62%,#e7eaef 100%)}
.illus--dark{border-radius:50%;background:radial-gradient(ellipse at 55% 40%,#7f8fb0 0%,#4a5674 40%,var(--ill-navy) 75%)}
.illus--screen{border-radius:4px;border:1px solid #cfd6e0;background:linear-gradient(135deg,#ffffff 0%,#e9edf3 55%,#c6d3e6 100%)}
.icon{width:14px;height:14px;border-radius:50%;background:var(--white);border:1px solid #d6e6f8;display:flex;align-items:center;justify-content:center}
.ftitle{font-weight:900;font-size:9px;line-height:11px}
.fsub{color:var(--blue);font-size:4.6px;font-weight:700;line-height:6.5px}
.more{width:22px;height:7px;border:1px solid var(--blue);color:var(--blue);font-size:3.4px;font-weight:700;text-align:center;line-height:5px}

/* examples */
.examples{position:absolute;left:0;top:1790px;width:488px;height:305px;background:linear-gradient(135deg,#1573d8,#0e60c4 60%,#1a85e8);clip-path:polygon(0 30px,100% 0,100% 100%,0 100%)}
.ex-ghost{position:absolute;left:312px;top:1836px;font-weight:900;font-size:34px;color:rgba(255,255,255,.15)}
.pill{height:8px;background:var(--blue-dark);color:var(--white);font-size:3.6px;font-weight:700;text-align:center;line-height:8px}
.thumb{position:absolute;border-radius:1px;z-index:1}
.cap{color:var(--white);font-size:4.6px;font-weight:700}
.btn-white{background:var(--white);color:var(--blue);font-size:3.6px;font-weight:700;text-align:center;line-height:8px;height:8px}

/* sizes */
.sz-ghost{position:absolute;left:-4px;top:2118px;font-weight:900;font-size:32px;color:var(--faint)}
.body b{color:var(--blue)}

/* footer */
.footer{position:absolute;left:0;top:2618px;width:488px;height:116px;background:var(--navy);clip-path:polygon(0 22px,100% 0,100% 100%,0 100%)}
.footer-accent{position:absolute;left:300px;top:2612px;width:188px;height:22px;background:var(--blue);clip-path:polygon(0 60%,100% 0,100% 100%)}
.f-logo{left:30px;top:2667px}
.socials{position:absolute;left:210px;top:2665px;display:flex;gap:4px}
.socials span{width:9px;height:9px;border-radius:50%;border:1px solid var(--white)}
.f-links{position:absolute;left:210px;top:2694px;display:flex;gap:8px;font-size:4.4px;color:var(--white)}
.f-copy{position:absolute;left:210px;top:2708px;font-size:3.6px;color:#9aa3b2}
.circle-blue{position:absolute;width:22px;height:22px;border-radius:50%;background:var(--blue);border:2px solid var(--white);box-shadow:0 1px 3px rgba(0,0,0,.2);z-index:2}
</style>
</head>
<body>

<!-- Concept A -->
<main class="page page--a">
  <header class="hero" role="img" aria-label="Dark blue glowing globe network background"></header>
  <div class="hero-accent"></div>
  <nav class="nav">
    <div class="logo"><span class="logo-mark"></span><span>KESTREL<small>MARKETING VIDEOS MADE FOR YOU</small></span></div>
    <div class="nav-links"><span>HOME</span><span>HOW IT WORKS</span><span>EXAMPLES</span><span>FAQ</span><span>CONTACT US</span><span>PRICING</span><span class="nav-btn">LOGIN</span><span class="nav-btn nav-btn--fill">SIGN UP</span></div>
  </nav>
  <h1 class="abs center hero-title">ATTENTION GRABBING <em>"VIRAL"</em><br>TYPE VIDEO ADS</h1>
  <p class="abs center hero-sub">ALL DELIVERED IN 24 HOURS</p>
  <div class="abs hero-btn">GET ONE FREE VIDEO SAMPLE NOW</div>
  <p class="abs center hero-note">No purchase necessary</p>

  <section>
    <div class="ghost-v">MARKETING</div>
    <h2 class="abs center h2" style="top:290px">PROMOTE ANYTHING</h2>
    <p class="abs center kicker" style="top:309px">ANYWHERE ON THE WEB</p>
    <p class="abs center body" style="top:320px">500 using static image ads with Circlet, Pictora, Workvine, Blinkly advertising plus<br>Stories! Turn them into VIDEO ADS and get higher conversion rates instantly.</p>
    <p class="abs create-1">WE CREATE</p>
    <p class="abs create-2">AWARD WINNING PROMOTIONAL</p>
    <p class="abs create-3">MARKETING VIDEOS</p>
    <p class="abs create-4">TO USE ALL OVER THE WEB</p>
    <svg class="abs" style="left:280px;top:368px" width="150" height="150" viewBox="0 0 150 150" aria-hidden="true">
      <circle cx="75" cy="75" r="62" fill="none" stroke="#1e88e5" stroke-width="1.5"/>
      <circle cx="75" cy="75" r="36" fill="none" stroke="#d6e6f8" stroke-width="1"/>
      <circle cx="75" cy="75" r="10" fill="#1e88e5"/>
    </svg>
    <span class="circle-blue" style="left:321px;top:384px"></span>
    <span class="circle-blue" style="left:344px;top:374px;background:#fff;border-color:#d6e6f8"></span>
    <span class="circle-blue" style="left:378px;top:384px"></span>
    <span class="circle-blue" style="left:305px;top:424px;background:#fff;border-color:#d6e6f8"></span>
    <span class="circle-blue" style="left:392px;top:424px;background:#fff;border-color:#d6e6f8"></span>
    <span class="circle-blue" style="left:321px;top:466px"></span>
    <span class="circle-blue" style="left:346px;top:476px;background:#fff;border-color:#d6e6f8"></span>
    <span class="circle-blue" style="left:378px;top:466px"></span>
  </section>

  <section class="features"></section>
  <p class="abs center ghost" style="top:590px">FEATURES</p>
  <h2 class="abs center h2" style="top:613px">OUR FEATURES</h2>

  <div class="illus illus--dark" style="left:70px;top:660px;width:150px;height:160px" role="img" aria-label="Illustration of a person beside a tree with a large tick"></div>
  <div class="abs icon" style="left:260px;top:691px"><svg width="7" height="7" viewBox="0 0 10 10"><path d="M1 5l3 3 5-6" fill="none" stroke="#1e88e5" stroke-width="1.6"/></svg></div>
  <h3 class="abs ftitle" style="left:260px;top:721px">DONE FOR YOU</h3>
  <p class="abs fsub" style="left:260px;top:736px">YOU DON'T LIFT A FINGER!</p>
  <p class="abs body" style="left:260px;top:748px">We make it super affordable and we DO IT ALL FOR YOU. You'll<br>receive a fully packaged, polished...</p>
  <div class="abs more" style="left:260px;top:787px">READ MORE</div>

  <div class="abs icon" style="left:65px;top:865px"><svg width="7" height="7" viewBox="0 0 10 10"><path d="M2 2h6M2 5h6M2 8h6" stroke="#1e88e5" stroke-width="1.4"/></svg></div>
  <h3 class="abs ftitle" style="left:65px;top:897px">PREMIUM CONTENT</h3>
  <p class="abs fsub" style="left:65px;top:913px">YOUR BUSINESS WILL LOOK SUPER HIGH-END &amp;<br>PROFESSIONAL</p>
  <p class="abs body" style="left:65px;top:936px">We have access to millions of premium video clips, fully paid<br>agents, Award Winning Videographers...</p>
  <div class="abs more" style="left:65px;top:973px">READ MORE</div>
  <div class="illus illus--screen" style="left:252px;top:860px;width:179px;height:133px" role="img" aria-label="Illustration of a person presenting a large document"></div>

  <div class="illus illus--round" style="left:38px;top:1070px;width:208px;height:112px" role="img" aria-label="Illustration of a person on a laptop beside license symbols"></div>
  <div class="abs icon" style="left:273px;top:1068px"><svg width="7" height="7" viewBox="0 0 10 10"><path d="M2 8l1-3 4-4 2 2-4 4z" fill="none" stroke="#1e88e5" stroke-width="1.2"/></svg></div>
  <h3 class="abs ftitle" style="left:273px;top:1099px">FULLY LICENSED TO YOU</h3>
  <p class="abs fsub" style="left:273px;top:1115px">YOU OWN ALL THE VIDEOS TO USE FOREVER -<br>CONSIDER THEM ASSETS</p>
  <p class="abs body" style="left:273px;top:1138px">The videos are yours to own now with a lifetime license<br>for unlimited sharing and use. Th...</p>
  <div class="abs more" style="left:273px;top:1176px">READ MORE</div>

  <div class="abs icon" style="left:65px;top:1259px"><svg width="7" height="7" viewBox="0 0 10 10"><circle cx="5" cy="5" r="4" fill="none" stroke="#1e88e5" stroke-width="1.2"/><path d="M4 3l3 2-3 2z" fill="#1e88e5"/></svg></div>
  <h3 class="abs ftitle" style="left:65px;top:1290px">PERFECT LENGTH FOR<br>MARKETING VIDEOS</h3>
  <p class="abs fsub" style="left:65px;top:1326px">STAND OUT FROM THE CROWD WITH VIDEO MARKETING</p>
  <p class="abs body" style="left:65px;top:1339px">Our Marketing Videos range from 15 seconds up to 50 seconds<br>in length. These are the recommende...</p>
  <div class="abs more" style="left:65px;top:1376px">READ MORE</div>
  <div class="illus illus--screen" style="left:270px;top:1267px;width:174px;height:101px" role="img" aria-label="Illustration of a person holding a video play window"></div>

  <div class="illus illus--dark" style="left:95px;top:1440px;width:141px;height:118px" role="img" aria-label="Illustration of a person beside a large smartphone"></div>
  <div class="abs icon" style="left:260px;top:1440px"><span style="width:5px;height:5px;background:#1e88e5;border-radius:50%"></span></div>
  <h3 class="abs ftitle" style="left:260px;top:1472px">CIRCLET VIDEO COVER</h3>
  <p class="abs fsub" style="left:260px;top:1488px">"WOW" CUSTOMERS WITH A BEAUTIFUL DESIGNED<br>CIRCLET COVER VIDEO FOR YOUR BUSINESS</p>
  <p class="abs body" style="left:260px;top:1511px">We can convert any video to a Circlet Video Cover for your<br>Circlet business page.</p>
  <div class="abs more" style="left:260px;top:1551px">READ MORE</div>

  <div class="abs icon" style="left:65px;top:1620px"><svg width="7" height="7" viewBox="0 0 10 10"><path d="M2 6V5a3 3 0 016 0v1" fill="none" stroke="#1e88e5" stroke-width="1.2"/><rect x="1.5" y="5.5" width="2" height="3" fill="#1e88e5"/><rect x="6.5" y="5.5" width="2" height="3" fill="#1e88e5"/></svg></div>
  <h3 class="abs ftitle" style="left:65px;top:1650px">BEST SUPPORT</h3>
  <p class="abs fsub" style="left:65px;top:1666px">WE ARE AVAILABLE TO YOU AT ALL TIMES FOR<br>ANY KIND OF SUPPORT</p>
  <p class="abs body" style="left:65px;top:1690px">Reach out anytime, anywhere. Our team of tech, marketing and<br>video experts are here to help you...</p>
  <div class="abs more" style="left:65px;top:1727px">READ MORE</div>
  <div class="illus illus--screen" style="left:265px;top:1605px;width:181px;height:140px" role="img" aria-label="Illustration of a support agent on a laptop screen"></div>

  <section class="examples"></section>
  <p class="ex-ghost">EXAMP</p>
  <h2 class="abs center h2" style="top:1853px;color:#fff">OUR EXAMPLES</h2>
  <div class="abs pill" style="left:204px;top:1889px;width:80px">SHOW ALL CATEGORY</div>
  <div class="thumb" style="left:57px;top:1921px;width:116px;height:80px;background:linear-gradient(135deg,#3c4a5e,#8795a8)" role="img" aria-label="Video still of a businessman presenting"></div>
  <div class="thumb" style="left:185px;top:1921px;width:118px;height:80px;background:linear-gradient(135deg,#1d2a3d,#4e6b8f)" role="img" aria-label="Video still of a team in a meeting with play button"></div>
  <div class="thumb" style="left:315px;top:1921px;width:116px;height:80px;background:linear-gradient(135deg,#e9d6dc,#b9a7b4)" role="img" aria-label="Video still of a dancer in a pink skirt"></div>
  <p class="abs cap" style="left:82px;top:2008px">MARKETING PROMO 1</p>
  <p class="abs cap" style="left:212px;top:2008px">MARKETING PROMO 2</p>
  <p class="abs cap" style="left:340px;top:2008px">MARKETING PROMO 3</p>
  <div class="abs btn-white" style="left:222px;top:2043px;width:44px">MORE INFO</div>

  <p class="sz-ghost">VIDEO SIZES</p>
  <h2 class="abs center h2" style="top:2130px">VIDEO SIZES AVAILABLE</h2>
  <p class="abs center body" style="top:2168px">Wide Screen Videos – This size is a standard video size that works best for pretty much anywhere<br>on the web <b>(1080x720)</b> included with all video purchases</p>
  <div class="thumb" style="left:57px;top:2208px;width:84px;height:53px;background:linear-gradient(135deg,#8a2b24,#d9d2cc)" role="img" aria-label="Wide video still of a red themed scene"></div>
  <div class="thumb" style="left:152px;top:2208px;width:84px;height:53px;background:linear-gradient(135deg,#0e1c30,#2f5a85)" role="img" aria-label="Wide video still of a dark tech scene"></div>
  <div class="thumb" style="left:252px;top:2208px;width:84px;height:53px;background:linear-gradient(135deg,#cfc6bf,#8d7f77)" role="img" aria-label="Wide video still of a woman in an office"></div>
  <div class="thumb" style="left:347px;top:2208px;width:80px;height:53px;background:linear-gradient(135deg,#0b1f3a,#2c6aa8)" role="img" aria-label="Wide video still of a blue digital scene"></div>
  <p class="abs center body" style="top:2280px">Square Videos that work best on CIRCLET (Square is <b>1080 X 1080</b>)<br>Convert any video to this size for an additional fee of $29</p>
  <div class="thumb" style="left:57px;top:2322px;width:84px;height:80px;background:linear-gradient(135deg,#d9c7b4,#6d5a4c)" role="img" aria-label="Square video still of a man holding a tablet"></div>
  <div class="thumb" style="left:152px;top:2322px;width:84px;height:80px;background:linear-gradient(135deg,#1b2736,#56708e)" role="img" aria-label="Square video still of a video wall"></div>
  <div class="thumb" style="left:252px;top:2322px;width:84px;height:80px;background:linear-gradient(135deg,#0a1a30,#2b73c0)" role="img" aria-label="Square video still of a glowing hologram in hands"></div>
  <div class="thumb" style="left:347px;top:2322px;width:80px;height:80px;background:linear-gradient(135deg,#efe6dc,#b8a18c)" role="img" aria-label="Square video still of a smiling woman"></div>
  <p class="abs center body" style="top:2420px">Vertical Videos that work best on STORIES for Circlet, Pictora and Blinkly <b>(1080 X 1920)</b><br>Convert any video to this size for an additional fee of $39</p>
  <div class="thumb" style="left:57px;top:2455px;width:84px;height:124px;background:linear-gradient(160deg,#e8dccf,#9c7c66)" role="img" aria-label="Vertical video still of a woman with shopping bags"></div>
  <div class="thumb" style="left:152px;top:2455px;width:84px;height:124px;background:linear-gradient(160deg,#ece6df,#8e7868)" role="img" aria-label="Vertical video still of a woman shopping"></div>
  <div class="thumb" style="left:252px;top:2455px;width:84px;height:124px;background:linear-gradient(160deg,#6c6f78,#7a1f2a)" role="img" aria-label="Vertical video still of a football player"></div>
  <div class="thumb" style="left:347px;top:2455px;width:80px;height:124px;background:linear-gradient(160deg,#f0e9e2,#b59c86)" role="img" aria-label="Vertical video still of a woman smiling"></div>

  <div class="footer-accent"></div>
  <footer class="footer"></footer>
  <div class="abs logo f-logo"><span class="logo-mark"></span><span>KESTREL<small>MARKETING VIDEOS MADE FOR YOU</small></span></div>
  <div class="socials"><span></span><span></span><span></span><span></span><span></span></div>
  <div class="f-links"><span>How It Works</span><span>Term Of Service</span><span>Privacy Policy</span><span>Cookies Policy</span></div>
  <p class="f-copy">© Copyright 2019 Kestrel Marketing Videos All Rights Reserved · Privacy policy</p>
</main>

<!-- Concept B -->
<main class="page page--b">
  <header class="hero" role="img" aria-label="Hands holding a smartphone in front of a wall of video screens"></header>
  <div class="hero-accent"></div>
  <nav class="nav">
    <div class="logo"><span class="logo-mark"></span><span>KESTREL<small>MARKETING VIDEOS MADE FOR YOU</small></span></div>
    <div class="nav-links"><span>HOME</span><span>HOW IT WORKS</span><span>EXAMPLES</span><span>FAQ</span><span>CONTACT US</span><span>PRICING</span><span class="nav-btn">LOGIN</span><span class="nav-btn nav-btn--fill">SIGN UP</span></div>
  </nav>
  <h1 class="abs center hero-title">ATTENTION GRABBING <em>"VIRAL"</em><br>TYPE VIDEO ADS</h1>
  <p class="abs center hero-sub">ALL DELIVERED IN 24 HOURS</p>
  <div class="abs hero-btn">GET ONE FREE VIDEO SAMPLE NOW</div>
  <p class="abs center hero-note">No purchase necessary</p>

  <section>
    <div class="ghost-v">MARKETING</div>
    <h2 class="abs center h2" style="top:290px">PROMOTE ANYTHING</h2>
    <p class="abs center kicker" style="top:309px">ANYWHERE ON THE WEB</p>
    <p class="abs center body" style="top:320px">500 using static image ads with Circlet, Pictora, Workvine, Blinkly advertising plus<br>Stories! Turn them into VIDEO ADS and get higher conversion rates instantly.</p>
    <p class="abs create-1">WE CREATE</p>
    <p class="abs create-2">AWARD WINNING PROMOTIONAL</p>
    <p class="abs create-3">MARKETING VIDEOS</p>
    <p class="abs create-4">TO USE ALL OVER THE WEB</p>
    <svg class="abs" style="left:280px;top:368px" width="150" height="150" viewBox="0 0 150 150" aria-hidden="true">
      <circle cx="75" cy="75" r="62" fill="none" stroke="#1e88e5" stroke-width="1.5"/>
      <circle cx="75" cy="75" r="36" fill="none" stroke="#d6e6f8" stroke-width="1"/>
      <circle cx="75" cy="75" r="10" fill="#1e88e5"/>
    </svg>
    <span class="circle-blue" style="left:321px;top:384px"></span>
    <span class="circle-blue" style="left:344px;top:374px;background:#fff;border-color:#d6e6f8"></span>
    <span class="circle-blue" style="left:378px;top:384px"></span>
    <span class="circle-blue" style="left:305px;top:424px;background:#fff;border-color:#d6e6f8"></span>
    <span class="circle-blue" style="left:392px;top:424px;background:#fff;border-color:#d6e6f8"></span>
    <span class="circle-blue" style="left:321px;top:466px"></span>
    <span class="circle-blue" style="left:346px;top:476px;background:#fff;border-color:#d6e6f8"></span>
    <span class="circle-blue" style="left:378px;top:466px"></span>
  </section>

  <section class="features"></section>
  <p class="abs center ghost" style="top:590px">FEATURES</p>
  <h2 class="abs center h2" style="top:613px">OUR FEATURES</h2>

  <div class="illus illus--dark" style="left:70px;top:660px;width:150px;height:160px" role="img" aria-label="Illustration of a person beside a tree with a large tick"></div>
  <div class="abs icon" style="left:260px;top:691px"><svg width="7" height="7" viewBox="0 0 10 10"><path d="M1 5l3 3 5-6" fill="none" stroke="#1e88e5" stroke-width="1.6"/></svg></div>
  <h3 class="abs ftitle" style="left:260px;top:721px">DONE FOR YOU</h3>
  <p class="abs fsub" style="left:260px;top:736px">YOU DON'T LIFT A FINGER!</p>
  <p class="abs body" style="left:260px;top:748px">We make it super affordable and we DO IT ALL FOR YOU. You'll<br>receive a fully packaged, polished...</p>
  <div class="abs more" style="left:260px;top:787px">READ MORE</div>

  <div class="abs icon" style="left:65px;top:865px"><svg width="7" height="7" viewBox="0 0 10 10"><path d="M2 2h6M2 5h6M2 8h6" stroke="#1e88e5" stroke-width="1.4"/></svg></div>
  <h3 class="abs ftitle" style="left:65px;top:897px">PREMIUM CONTENT</h3>
  <p class="abs fsub" style="left:65px;top:913px">YOUR BUSINESS WILL LOOK SUPER HIGH-END &amp;<br>PROFESSIONAL</p>
  <p class="abs body" style="left:65px;top:936px">We have access to millions of premium video clips, fully paid<br>agents, Award Winning Videographers...</p>
  <div class="abs more" style="left:65px;top:973px">READ MORE</div>
  <div class="illus illus--screen" style="left:252px;top:860px;width:179px;height:133px" role="img" aria-label="Illustration of a person presenting a large document"></div>

  <div class="illus illus--round" style="left:38px;top:1070px;width:208px;height:112px" role="img" aria-label="Illustration of a person on a laptop beside license symbols"></div>
  <div class="abs icon" style="left:273px;top:1068px"><svg width="7" height="7" viewBox="0 0 10 10"><path d="M2 8l1-3 4-4 2 2-4 4z" fill="none" stroke="#1e88e5" stroke-width="1.2"/></svg></div>
  <h3 class="abs ftitle" style="left:273px;top:1099px">FULLY LICENSED TO YOU</h3>
  <p class="abs fsub" style="left:273px;top:1115px">YOU OWN ALL THE VIDEOS TO USE FOREVER -<br>CONSIDER THEM ASSETS</p>
  <p class="abs body" style="left:273px;top:1138px">The videos are yours to own now with a lifetime license<br>for unlimited sharing and use. Th...</p>
  <div class="abs more" style="left:273px;top:1176px">READ MORE</div>

  <div class="abs icon" style="left:65px;top:1259px"><svg width="7" height="7" viewBox="0 0 10 10"><circle cx="5" cy="5" r="4" fill="none" stroke="#1e88e5" stroke-width="1.2"/><path d="M4 3l3 2-3 2z" fill="#1e88e5"/></svg></div>
  <h3 class="abs ftitle" style="left:65px;top:1290px">PERFECT LENGTH FOR<br>MARKETING VIDEOS</h3>
  <p class="abs fsub" style="left:65px;top:1326px">STAND OUT FROM THE CROWD WITH VIDEO MARKETING</p>
  <p class="abs body" style="left:65px;top:1339px">Our Marketing Videos range from 15 seconds up to 50 seconds<br>in length. These are the recommende...</p>
  <div class="abs more" style="left:65px;top:1376px">READ MORE</div>
  <div class="illus illus--screen" style="left:270px;top:1267px;width:174px;height:101px" role="img" aria-label="Illustration of a person holding a video play window"></div>

  <div class="illus illus--dark" style="left:95px;top:1440px;width:141px;height:118px" role="img" aria-label="Illustration of a person beside a large smartphone"></div>
  <div class="abs icon" style="left:260px;top:1440px"><span style="width:5px;height:5px;background:#1e88e5;border-radius:50%"></span></div>
  <h3 class="abs ftitle" style="left:260px;top:1472px">CIRCLET VIDEO COVER</h3>
  <p class="abs fsub" style="left:260px;top:1488px">"WOW" CUSTOMERS WITH A BEAUTIFUL DESIGNED<br>CIRCLET COVER VIDEO FOR YOUR BUSINESS</p>
  <p class="abs body" style="left:260px;top:1511px">We can convert any video to a Circlet Video Cover for your<br>Circlet business page.</p>
  <div class="abs more" style="left:260px;top:1551px">READ MORE</div>

  <div class="abs icon" style="left:65px;top:1620px"><svg width="7" height="7" viewBox="0 0 10 10"><path d="M2 6V5a3 3 0 016 0v1" fill="none" stroke="#1e88e5" stroke-width="1.2"/><rect x="1.5" y="5.5" width="2" height="3" fill="#1e88e5"/><rect x="6.5" y="5.5" width="2" height="3" fill="#1e88e5"/></svg></div>
  <h3 class="abs ftitle" style="left:65px;top:1650px">BEST SUPPORT</h3>
  <p class="abs fsub" style="left:65px;top:1666px">WE ARE AVAILABLE TO YOU AT ALL TIMES FOR<br>ANY KIND OF SUPPORT</p>
  <p class="abs body" style="left:65px;top:1690px">Reach out anytime, anywhere. Our team of tech, marketing and<br>video experts are here to help you...</p>
  <div class="abs more" style="left:65px;top:1727px">READ MORE</div>
  <div class="illus illus--screen" style="left:265px;top:1605px;width:181px;height:140px" role="img" aria-label="Illustration of a support agent on a laptop screen"></div>

  <section class="examples"></section>
  <p class="ex-ghost">EXAMP</p>
  <h2 class="abs center h2" style="top:1853px;color:#fff">OUR EXAMPLES</h2>
  <div class="abs pill" style="left:204px;top:1889px;width:80px">SHOW ALL CATEGORY</div>
  <div class="thumb" style="left:57px;top:1921px;width:116px;height:80px;background:linear-gradient(135deg,#3c4a5e,#8795a8)" role="img" aria-label="Video still of a businessman presenting"></div>
  <div class="thumb" style="left:185px;top:1921px;width:118px;height:80px;background:linear-gradient(135deg,#1d2a3d,#4e6b8f)" role="img" aria-label="Video still of a team in a meeting with play button"></div>
  <div class="thumb" style="left:315px;top:1921px;width:116px;height:80px;background:linear-gradient(135deg,#e9d6dc,#b9a7b4)" role="img" aria-label="Video still of a dancer in a pink skirt"></div>
  <p class="abs cap" style="left:82px;top:2008px">MARKETING PROMO 1</p>
  <p class="abs cap" style="left:212px;top:2008px">MARKETING PROMO 2</p>
  <p class="abs cap" style="left:340px;top:2008px">MARKETING PROMO 3</p>
  <div class="abs btn-white" style="left:222px;top:2043px;width:44px">MORE INFO</div>

  <p class="sz-ghost">VIDEO SIZES</p>
  <h2 class="abs center h2" style="top:2130px">VIDEO SIZES AVAILABLE</h2>
  <p class="abs center body" style="top:2168px">Wide Screen Videos – This size is a standard video size that works best for pretty much anywhere<br>on the web <b>(1080x720)</b> included with all video purchases</p>
  <div class="thumb" style="left:57px;top:2208px;width:84px;height:53px;background:linear-gradient(135deg,#8a2b24,#d9d2cc)" role="img" aria-label="Wide video still of a red themed scene"></div>
  <div class="thumb" style="left:152px;top:2208px;width:84px;height:53px;background:linear-gradient(135deg,#0e1c30,#2f5a85)" role="img" aria-label="Wide video still of a dark tech scene"></div>
  <div class="thumb" style="left:252px;top:2208px;width:84px;height:53px;background:linear-gradient(135deg,#cfc6bf,#8d7f77)" role="img" aria-label="Wide video still of a woman in an office"></div>
  <div class="thumb" style="left:347px;top:2208px;width:80px;height:53px;background:linear-gradient(135deg,#0b1f3a,#2c6aa8)" role="img" aria-label="Wide video still of a blue digital scene"></div>
  <p class="abs center body" style="top:2280px">Square Videos that work best on CIRCLET (Square is <b>1080 X 1080</b>)<br>Convert any video to this size for an additional fee of $29</p>
  <div class="thumb" style="left:57px;top:2322px;width:84px;height:80px;background:linear-gradient(135deg,#d9c7b4,#6d5a4c)" role="img" aria-label="Square video still of a man holding a tablet"></div>
  <div class="thumb" style="left:152px;top:2322px;width:84px;height:80px;background:linear-gradient(135deg,#1b2736,#56708e)" role="img" aria-label="Square video still of a video wall"></div>
  <div class="thumb" style="left:252px;top:2322px;width:84px;height:80px;background:linear-gradient(135deg,#0a1a30,#2b73c0)" role="img" aria-label="Square video still of a glowing hologram in hands"></div>
  <div class="thumb" style="left:347px;top:2322px;width:80px;height:80px;background:linear-gradient(135deg,#efe6dc,#b8a18c)" role="img" aria-label="Square video still of a smiling woman"></div>
  <p class="abs center body" style="top:2420px">Vertical Videos that work best on STORIES for Circlet, Pictora and Blinkly <b>(1080 X 1920)</b><br>Convert any video to this size for an additional fee of $39</p>
  <div class="thumb" style="left:57px;top:2455px;width:84px;height:124px;background:linear-gradient(160deg,#e8dccf,#9c7c66)" role="img" aria-label="Vertical video still of a woman with shopping bags"></div>
  <div class="thumb" style="left:152px;top:2455px;width:84px;height:124px;background:linear-gradient(160deg,#ece6df,#8e7868)" role="img" aria-label="Vertical video still of a woman shopping"></div>
  <div class="thumb" style="left:252px;top:2455px;width:84px;height:124px;background:linear-gradient(160deg,#6c6f78,#7a1f2a)" role="img" aria-label="Vertical video still of a football player"></div>
  <div class="thumb" style="left:347px;top:2455px;width:80px;height:124px;background:linear-gradient(160deg,#f0e9e2,#b59c86)" role="img" aria-label="Vertical video still of a woman smiling"></div>

  <div class="footer-accent"></div>
  <footer class="footer"></footer>
  <div class="abs logo f-logo"><span class="logo-mark"></span><span>KESTREL<small>MARKETING VIDEOS MADE FOR YOU</small></span></div>
  <div class="socials"><span></span><span></span><span></span><span></span><span></span></div>
  <div class="f-links"><span>How It Works</span><span>Term Of Service</span><span>Privacy Policy</span><span>Cookies Policy</span></div>
  <p class="f-copy">© Copyright 2019 Kestrel Marketing Videos All Rights Reserved · Privacy policy</p>
</main>

</body>
</html>
```